Calder Vossik - Cinematographer

NEED:
I'm looking for a sleek, professional, modern business card that will give give the recipient the impression that they can trust their production will go smoothly by hiring me. I will bring creativity and knowledge to their shoot, so that we can create powerful images.
I am looking for a card with a strong style and design ethos that could be expanded to a website and a full visual/graphic/design entity for me.
ABOUT ME:
I am a mid-twenties cinematographer, I work on music video, narrative short, commercial, and corporate projects. I blend the science and artistry of cameras and filmmaking to tell a story. I'm an artist, a technician, and a manager.
DESIGN:
I like sleek, simple design. Black, dark grays, white, dark navy, steel blues, I love cyan, but also cyan and red. I am not a fan of earthy tones. I generally prefer modern, san-serif fonts over serifs. My old logo was based on an aperture, a multi-blade device at the back of a lens that controls how much light passes through, but I made it with so many colors, that it doesn't necessarily lend itself to a specific color-scheme or design ethos. I liked that the aperture design provided a sense of the technical requirements of my job. I'm a fan of matte business cards, but am open to plenty of specialty print processes to make an outstanding card.
ATTACHED FILES:
My Old Rainbox Aperture Logo, plus a few designs I've tried playing around with, but am not tied to. I AM OPEN TO NEW DESIGNS, DO NOT FEEL TIED TO THIS.
**I've pulled my old logo down from the attached files, and instead attached other business cards I like, so as not to mislead you where I would like to go.
INFO:
Name: Calder Vossik
Job: Cinematographer
Email: ccvossik@lumenpost.net
Phone: 415.555.0193
Website: caldervossik.com
Updates
I'm adding some images of other cards that I like, and removing my old logo, since I'm looking for something new, and don't want that old logo to push anyone a certain direction.

```html
<!DOCTYPE html>
<html lang="en">
<head>
<meta charset="utf-8">
<title>Calder Vossik — Cinematographer Business Card</title>
<link rel="stylesheet" href="https://fonts.googleapis.com/css2?family=Archivo:wght@400;700;800&display=swap">
<style>
  :root {
    --backdrop: #d6d6d6;
    --card: #050505;
    --card-edge: #141414;
    --ink-white: #ffffff;
    --ink-gray: #9a9a9a;
    --ink-contact: #f2f2f2;
    --mark-gray: #5a5a5a;
    --deco-gray: #1b1b1b;
    --accent-blue: #2a8fd8;
    --rule-red: #3a1414;
  }
  * { margin: 0; padding: 0; box-sizing: border-box; }
  html, body {
    width: 1200px;
    height: 926px;
    overflow: hidden;
    background: var(--backdrop);
    font-family: "Archivo", Arial, sans-serif;
  }
  .canvas {
    position: relative;
    width: 1200px;
    height: 926px;
  }
  .card {
    position: absolute;
    left: 240px;
    width: 720px;
    height: 411px;
    background: var(--card);
    border: 1px solid var(--card-edge);
    overflow: hidden;
    box-shadow: 0 10px 30px rgba(0,0,0,0.25);
  }
  .card--front { top: 32px; }
  .card--back { top: 483px; }

  /* Front */
  .front-name {
    position: absolute;
    inset: 0;
    display: flex;
    align-items: center;
    justify-content: center;
    font-weight: 800;
    font-size: 40px;
    letter-spacing: 2px;
    text-transform: uppercase;
    color: var(--mark-gray);
  }

  /* Back */
  .back-decoration {
    position: absolute;
    left: 300px;
    top: 40px;
    font-weight: 800;
    font-size: 118px;
    line-height: 0.95;
    text-transform: uppercase;
    color: var(--deco-gray);
    white-space: nowrap;
  }
  .identity {
    position: absolute;
    left: 250px;
    top: 104px;
    text-align: right;
  }
  .identity__name {
    font-weight: 700;
    font-size: 27px;
    letter-spacing: 2px;
    text-transform: uppercase;
    color: var(--ink-white);
  }
  .identity__role {
    font-weight: 400;
    font-size: 16px;
    letter-spacing: 1px;
    color: var(--ink-gray);
    margin-top: 2px;
  }
  .identity__rule {
    position: absolute;
    left: 40px;
    right: 0;
    top: 40px;
    height: 1px;
    background: linear-gradient(90deg, transparent, var(--rule-red) 40%, #555 100%);
  }
  .contact {
    position: absolute;
    left: 50px;
    top: 250px;
    list-style: none;
  }
  .contact__item {
    display: flex;
    align-items: center;
    gap: 12px;
    font-size: 16px;
    color: var(--ink-contact);
    margin-bottom: 9px;
  }
  .contact__icon {
    width: 14px;
    height: 14px;
    flex: none;
  }
</style>
</head>
<body>
<main class="canvas">

  <section class="card card--front" aria-label="Card front">
    <div class="front-name">Calder Vossik</div>
  </section>

  <section class="card card--back" aria-label="Card back">
    <div class="back-decoration" aria-hidden="true">Calder<br>Vossik</div>

    <div class="identity">
      <h1 class="identity__name">Calder Vossik</h1>
      <span class="identity__rule"></span>
      <p class="identity__role">cinematographer</p>
    </div>

    <ul class="contact">
      <li class="contact__item">
        <svg class="contact__icon" viewBox="0 0 14 14" aria-hidden="true">
          <rect x="1" y="3" width="12" height="8" fill="var(--accent-blue)"/>
          <path d="M1 3 L7 8 L13 3" fill="none" stroke="var(--card)" stroke-width="1"/>
        </svg>
        ccvossik@lumenpost.net
      </li>
      <li class="contact__item">
        <svg class="contact__icon" viewBox="0 0 14 14" aria-hidden="true">
          <rect x="4" y="1" width="6" height="12" rx="1" fill="none" stroke="var(--accent-blue)" stroke-width="1.4"/>
          <rect x="6" y="10.5" width="2" height="1" fill="var(--accent-blue)"/>
        </svg>
        415.555.0193
      </li>
      <li class="contact__item">
        <svg class="contact__icon" viewBox="0 0 14 14" aria-hidden="true">
          <circle cx="7" cy="7" r="6" fill="none" stroke="var(--accent-blue)" stroke-width="1.3"/>
          <ellipse cx="7" cy="7" rx="2.5" ry="6" fill="none" stroke="var(--accent-blue)" stroke-width="1"/>
          <line x1="1" y1="7" x2="13" y2="7" stroke="var(--accent-blue)" stroke-width="1"/>
        </svg>
        www.caldervossik.com
      </li>
    </ul>
  </section>

</main>
</body>
</html>
```